Consulting company business cards

We have a base design, but would be willing to update. We have a new logo/"tag" that needs to be added. Current business card design is attached for reference into our "style."

Industry/Entity Type

Business

Contact Information for Business Card

Should contain name and title, office number, mobile number if appropriate, e-mail, website, physical address, and company logo.

Font styles to use
Other font styles liked:
• See current card design on KorvandBCard

Colors
0455a3
85acd3
aaaaaa

Requirements
Must have
• Our colors are navy blue, gray, and a lighter blue
Nice to have
• Design that I can easily drop in new names/titles as we hire employees.

```html
<!DOCTYPE html>
<html lang="en">
<head>
<meta charset="utf-8">
<title>Harlow Business Cards</title>
<link href="https://fonts.googleapis.com/css2?family=Montserrat:wght@400;500;600;800&display=swap" rel="stylesheet">
<style>
  :root {
    --navy: #0b3350;
    --light-blue: #85acd3;
    --bright-blue: #29a8e0;
    --gray: #aaaaaa;
    --slate: #6f8aa3;
    --white: #ffffff;
    --backdrop: #2e2f31;
    --text-dark: #14324b;
  }
  * { box-sizing: border-box; margin: 0; padding: 0; }
  html, body {
    width: 1200px; height: 900px; overflow: hidden;
    background: var(--backdrop);
    font-family: "Montserrat", sans-serif;
  }
  .canvas {
    width: 1200px; height: 900px;
    display: flex; flex-direction: column; align-items: center; justify-content: center;
    gap: 50px;
  }
  .card {
    width: 620px; height: 354px;
    border-radius: 22px;
    position: relative;
    overflow: hidden;
  }
  /* Front */
  .card-front { background: var(--navy); color: var(--white); }
  .brand-lockup {
    position: absolute; left: 110px; top: 92px;
  }
  .brand-row { display: flex; align-items: center; gap: 16px; }
  .brand-name {
    font-weight: 800; font-size: 78px; letter-spacing: 3px; line-height: 1;
    color: var(--white);
  }
  .brand-dot {
    width: 58px; height: 58px; border-radius: 50%;
    background: var(--light-blue);
  }
  .brand-tagline {
    margin-top: 10px;
    font-size: 17px; font-weight: 500; letter-spacing: 3.2px;
    color: var(--slate);
  }
  .brand-tagline .domain { color: var(--light-blue); letter-spacing: 0.5px; text-transform: none; font-weight: 500; }
  .front-web {
    position: absolute; left: 0; right: 0; bottom: 58px;
    text-align: center; font-size: 18px; font-weight: 500; letter-spacing: 0.5px;
  }
  .front-web strong { font-weight: 600; }
  /* Back */
  .card-back { background: var(--white); color: var(--text-dark); }
  .mascot-art {
    position: absolute; left: 96px; top: 92px;
    width: 200px; height: 186px;
    border-radius: 40% 30% 18% 45%;
    background: var(--navy);
  }
  .divider {
    position: absolute; left: 336px; top: 72px;
    width: 1.5px; height: 210px; background: var(--gray);
  }
  .details {
    position: absolute; left: 360px; top: 74px; width: 250px;
  }
  .person-name {
    font-size: 22px; font-weight: 800; color: var(--bright-blue); letter-spacing: 0.5px; line-height: 1.1;
  }
  .person-title { font-size: 14px; font-weight: 500; letter-spacing: 0.8px; margin-top: 2px; }
  .address { margin-top: 14px; font-size: 13.5px; line-height: 1.35; }
  .contacts { list-style: none; margin-top: 12px; font-size: 13.5px; line-height: 1.45; }
  .contacts li { display: flex; align-items: center; gap: 8px; }
  .contacts svg { width: 11px; height: 11px; flex: none; }
  .contacts .domain { color: var(--bright-blue); font-weight: 600; }
</style>
</head>
<body>
<main class="canvas">
  <section class="card card-front">
    <div class="brand-lockup">
      <div class="brand-row">
        <span class="brand-name">HARLOW</span>
        <span class="brand-dot"></span>
      </div>
      <p class="brand-tagline">A CLOUD CONSULTING COMPANY</p>
    </div>
    <p class="front-web">www.<strong>HARLOWTECH</strong>.com</p>
  </section>

  <section class="card card-back">
    <div class="mascot-art" role="img" aria-label="Navy silhouette illustration of a dog's head in profile"></div>
    <div class="divider"></div>
    <div class="details">
      <h1 class="person-name">RENATA KORVAND</h1>
      <p class="person-title">OFFICE MANAGER</p>
      <p class="address">1870 W 54th St<br>Carmel, IN 46032</p>
      <ul class="contacts">
        <li>
          <svg viewBox="0 0 12 12"><path d="M2.5 1 L4.5 1 L5 3.5 L3.8 4.4 Q5 7 7.6 8.2 L8.5 7 L11 7.5 L11 9.5 Q10.5 11 9 11 Q1 10 1 2.5 Q1 1 2.5 1Z" fill="var(--bright-blue)"/></svg>
          317.555.0148
        </li>
        <li>
          <svg viewBox="0 0 12 12"><rect x="3" y="0.8" width="6" height="10.4" rx="1.2" fill="none" stroke="var(--bright-blue)" stroke-width="1.4"/><circle cx="6" cy="9.2" r="0.7" fill="var(--bright-blue)"/></svg>
          317.555.0172
        </li>
        <li>
          <svg viewBox="0 0 12 12"><rect x="0.8" y="2.3" width="10.4" height="7.4" rx="1" fill="none" stroke="var(--bright-blue)" stroke-width="1.3"/><path d="M1 2.8 L6 6.6 L11 2.8" fill="none" stroke="var(--bright-blue)" stroke-width="1.2"/></svg>
          rkorvand@harlowtech.com
        </li>
        <li>
          <svg viewBox="0 0 12 12"><circle cx="6" cy="6" r="5" fill="none" stroke="var(--bright-blue)" stroke-width="1.2"/><ellipse cx="6" cy="6" rx="2.2" ry="5" fill="none" stroke="var(--bright-blue)" stroke-width="1"/><path d="M1 6 H11" stroke="var(--bright-blue)" stroke-width="1"/></svg>
          <span>www.<span class="domain">HARLOWTECH</span>.com</span>
        </li>
      </ul>
    </div>
  </section>
</main>
</body>
</html>
```